Diagram of Hollowmere’s history for website

This project is to design the attached diagram along the lines of the attached image but in our branding - style guide attached. The diagram will be going on the Hollowmere website - www.hollowmere.au.

```html
<!DOCTYPE html>
<html lang="en">
<head>
<meta charset="utf-8">
<title>Hollowmere – Our History</title>
<link rel="stylesheet" href="https://fonts.googleapis.com/css2?family=Poppins:wght@300;400;500;600&display=swap">
<style>
  :root {
    --ink: #333333;
    --body: #4a4a4a;
    --band: #e3e9e9;
    --y2017: #667d80;
    --y2018: #84a1a8;
    --y2019: #586f58;
    --y2021: #6f8f72;
    --y2022: #a98b7d;
    --y2023: #d4a891;
  }
  html, body { margin: 0; padding: 0; overflow: hidden; background: #ffffff; }
  .history {
    position: relative;
    width: 1200px;
    height: 708px;
    overflow: hidden;
    font-family: "Poppins", sans-serif;
    background: #ffffff;
  }
  .timeline-art { position: absolute; inset: 0; }
  .brand {
    position: absolute; left: 134px; top: 74px;
    display: flex; align-items: center; gap: 8px;
    font-size: 20px; font-weight: 600; color: var(--y2017);
  }
  .brand-dot { width: 14px; height: 14px; border-radius: 50%; background: var(--y2023); }
  .page-title {
    position: absolute; left: 94px; top: 152px; margin: 0;
    font-size: 28px; font-weight: 600; color: var(--ink); letter-spacing: -0.2px;
  }
  .entry { position: absolute; }
  .milestone {
    margin: 0; font-size: 17px; font-weight: 600; line-height: 1.0;
  }
  .note {
    margin: 0; font-size: 10px; font-weight: 300; line-height: 1.22; color: var(--body);
  }
  .note.small { font-size: 8.6px; }
  .year {
    position: absolute; margin: 0;
    font-size: 31px; font-weight: 600; line-height: 1;
  }
  .c2017 { color: var(--y2017); }
  .c2018 { color: var(--y2018); }
  .c2019 { color: var(--y2019); }
  .c2021 { color: var(--y2021); }
  .c2022 { color: var(--y2022); }
  .c2023 { color: var(--y2023); }
</style>
</head>
<body>
<main class="history">
  <svg class="timeline-art" width="1200" height="708" viewBox="0 0 1200 708" aria-hidden="true">
    <rect x="94" y="363" width="1036" height="14" fill="var(--band)"/>
    <polygon points="1130,353 1147,370 1130,387" fill="var(--band)"/>
    <line x1="93" y1="370" x2="93" y2="568" stroke="var(--y2017)" stroke-width="1.2"/>
    <line x1="263" y1="370" x2="263" y2="267" stroke="var(--y2018)" stroke-width="1.2"/>
    <line x1="433" y1="370" x2="433" y2="490" stroke="var(--y2019)" stroke-width="1.2"/>
    <line x1="602" y1="370" x2="602" y2="256" stroke="var(--y2021)" stroke-width="1.2"/>
    <line x1="772" y1="370" x2="772" y2="649" stroke="var(--y2022)" stroke-width="1.2"/>
    <line x1="940" y1="370" x2="940" y2="58" stroke="var(--y2023)" stroke-width="1.2"/>
    <g stroke="#ffffff" stroke-width="1.5">
      <circle cx="93" cy="370" r="11.5" fill="var(--y2017)"/>
      <circle cx="93" cy="568" r="11.5" fill="var(--y2017)"/>
      <circle cx="263" cy="370" r="11.5" fill="var(--y2018)"/>
      <circle cx="263" cy="267" r="11.5" fill="var(--y2018)"/>
      <circle cx="433" cy="370" r="11.5" fill="var(--y2019)"/>
      <circle cx="433" cy="490" r="11.5" fill="var(--y2019)"/>
      <circle cx="602" cy="370" r="11.5" fill="var(--y2021)"/>
      <circle cx="602" cy="256" r="11.5" fill="var(--y2021)"/>
      <circle cx="772" cy="370" r="11.5" fill="var(--y2022)"/>
      <circle cx="772" cy="649" r="11.5" fill="var(--y2022)"/>
      <circle cx="940" cy="370" r="11.5" fill="var(--y2023)"/>
      <circle cx="940" cy="58" r="11.5" fill="var(--y2023)"/>
      <circle cx="940" cy="100" r="11.5" fill="var(--y2023)"/>
      <circle cx="940" cy="171" r="11.5" fill="var(--y2023)"/>
      <circle cx="940" cy="225" r="11.5" fill="var(--y2023)"/>
      <circle cx="940" cy="280" r="11.5" fill="var(--y2023)"/>
    </g>
  </svg>

  <div class="brand"><span class="brand-dot"></span>Hollowmere</div>
  <h1 class="page-title">Our History</h1>

  <!-- 2017 -->
  <section class="entry" style="left:113px; top:386px;">
    <h2 class="milestone c2017">Hollowmere<br>Commences</h2>
    <p class="note small" style="margin-top:6px;">Maren started the business<br>with 25 years' experience<br>working for government &amp;<br>non-government disability<br>&amp;community services. Our first<br>office is in Elmford</p>
  </section>
  <section class="entry" style="left:113px; top:499px;">
    <h2 class="milestone c2017">Carewell Provider</h2>
    <p class="note small" style="margin-top:6px;">Hollowmere becomes a Carewell<br>Registered provider</p>
  </section>
  <p class="year c2017" style="left:112px; top:553px;">2017</p>

  <!-- 2018 -->
  <section class="entry" style="left:290px; top:254px;">
    <h2 class="milestone c2018">Clinic Expansion</h2>
    <p class="note" style="margin-top:7px;">Hollowmere moves offices twice<br>in Elmford due to growth &amp;<br>expansion. Clinic established</p>
  </section>
  <p class="year c2018" style="left:290px; top:325px;">2018</p>

  <!-- 2019 -->
  <section class="entry" style="left:456px; top:386px;">
    <h2 class="milestone c2019">Move to<br>Ashbury</h2>
    <p class="note" style="margin-top:6px;">Hollowmere moves to<br>Ashbury due to further<br>growth &amp; expansion</p>
  </section>
  <p class="year c2019" style="left:456px; top:469px;">2019</p>

  <!-- 2021 -->
  <section class="entry" style="left:629px; top:243px;">
    <h2 class="milestone c2021">Impact Certified</h2>
    <p class="note" style="margin-top:7px;">Hollowmere becomes an accredited<br>Impact Certified business having met the<br>highest standards of environmental,<br>social &amp; community performance</p>
  </section>
  <p class="year c2021" style="left:629px; top:325px;">2021</p>

  <!-- 2022 -->
  <section class="entry" style="left:795px; top:386px;">
    <h2 class="milestone c2022">Vantara Best<br>of Business</h2>
    <p class="note" style="margin-top:6px;">Hollowmere wins the Vantara<br>Best of Business Award (Vic)<br>for building communities</p>
  </section>
  <section class="entry" style="left:795px; top:480px;">
    <h2 class="milestone c2022">Move to Kestrel Park</h2>
    <p class="note" style="margin-top:7px;">Hollowmere moves to<br>a larger premises in<br>Kestrel Park</p>
  </section>
  <section class="entry" style="left:795px; top:549px;">
    <h2 class="milestone c2022">Partnership</h2>
    <p class="note" style="margin-top:7px;">Partnerships established with<br>Lagoonside School for Children with<br>Disability &amp; Wirrin Centre<br>(Eastfield University)</p>
  </section>
  <p class="year c2022" style="left:795px; top:628px;">2022</p>

  <!-- 2023 -->
  <section class="entry" style="left:967px; top:46px;">
    <h2 class="milestone c2023">Rebranding</h2>
    <p class="note" style="margin-top:5px;">Hollowmere rebranded</p>
  </section>
  <section class="entry" style="left:967px; top:89px;">
    <h2 class="milestone c2023">Community<br>Respect Plan (CRP)</h2>
    <p class="note" style="margin-top:6px;">Hollowmere's Reflect CRP<br>developed &amp; endorsed</p>
  </section>
  <section class="entry" style="left:967px; top:160px;">
    <h2 class="milestone c2023">Client Advisory Group</h2>
    <p class="note" style="margin-top:6px;">Hollowmere's Client Advisory<br>Group commences</p>
  </section>
  <section class="entry" style="left:967px; top:214px;">
    <h2 class="milestone c2023">E-Learning Platform</h2>
    <p class="note" style="margin-top:6px;">Hollowmere e-learning<br>platform launched</p>
  </section>
  <section class="entry" style="left:967px; top:269px;">
    <h2 class="milestone c2023">Pride Mark</h2>
    <p class="note" style="margin-top:6px;">Hollowmere achieves Pride Mark<br>accreditation</p>
  </section>
  <p class="year c2023" style="left:967px; top:325px;">2023</p>
</main>
</body>
</html>
```